New Payments Start-up requires Logo, Style Guide and Web Site Design

We need a logo, style guide (colour templates etc.) and marketing web-site (HTML/CSS styling) for Fenwu, a new account-to-account payment product for use in the Single European Payment Area (SEPA).

The design is for the product only, not a company brand. We're looking for basic palette and style guidelines also. The web site need only be a basic responsive cross-platform design and layout. We will produce our own content.

We have no requirements for specific colours or logo styles. It is a financial product, however, so should not appear too quirky or untrustworthy.

The product is still in the early phases of development, so we're not able to provide pictures or other content.

As a little more detail on how things work, though, our end customers will arrive at our site through redirection from our merchant partners (a number of whom are large multi-national companies) who have offered our services as an alternative to credit card payments. They will be able to set up a SEPA direct debit mandate online in just a few pages, secure that with a password and use it to pay both immediately and in future with a simple confirmation of the password… a quick, easy checkout.

Because we work with large customer in the payments space, whilst we’d like the brand to be modern and appealing, it has to engender trust and stability. Whilst this product is new and in start-up phase, our company has been in alternative payments for nearly 10 years and have strong products in Europe in the Pre-Paid Zelo/TrevinCard and Voucher space. We'd like to treat this separately, however, which is why we've briefed accordingly.

Reason: Apologies for the extension, but I had a couple of designers contact me to say they had completed work but were unable to submit because time ran out. I'll only extend this once, though, because we need to get cracking on the project. Many thanks Jem

Target Market(s)

European alternative payment customers

Industry/Entity Type

Financial

Logo Text

fenwu

Coding

Coded - Design and coding required

Number of Pages Required

1 page

Font styles to use
Sans Serif

```html
<!DOCTYPE html>
<html lang="en">
<head>
<meta charset="utf-8">
<title>fenwu — account-to-account payments</title>
<link rel="stylesheet" href="https://fonts.googleapis.com/css2?family=Open+Sans:wght@400;600;700&family=Roboto+Slab:wght@300;400&display=swap">
<style>
:root{
  --blue:#1b9ad6;
  --blue-dark:#1487bd;
  --orange:#f6a524;
  --ink:#333840;
  --text:#6b6f75;
  --light:#9a9ea3;
  --line:#e4e6e8;
  --white:#ffffff;
  --hero-a:#6b4a45;
  --hero-b:#2f3b52;
  --city-a:#3c4650;
  --city-b:#222a33;
  --testi-a:#8a7a6a;
  --testi-b:#3a3530;
}
*{box-sizing:border-box;margin:0;padding:0}
html,body{width:1200px;height:3249px;overflow:hidden}
body{font-family:"Open Sans",Arial,sans-serif;color:var(--text);background:var(--white);position:relative}
.slab{font-family:"Roboto Slab",Georgia,serif;font-weight:300;color:var(--ink)}
section,header,footer{position:absolute;left:0;width:1200px}
.center{text-align:center}
.btn{display:inline-block;background:var(--blue);color:var(--white);font-size:15px;font-weight:600;height:50px;line-height:50px;padding:0 36px;border-radius:2px}

/* hero */
.hero{top:0;height:650px;background:radial-gradient(ellipse at 35% 25%,#b97a62 0%,transparent 45%),linear-gradient(135deg,var(--hero-a) 0%,#4c4b5c 50%,var(--hero-b) 100%)}
.hero-shade{position:absolute;inset:0;background:rgba(20,25,40,.25)}
.nav{position:absolute;top:36px;left:52px;right:52px;display:flex;align-items:center}
.brand{font-size:46px;font-weight:400;color:var(--blue);letter-spacing:-1px}
.menu{margin-left:auto;display:flex;gap:52px;align-items:center}
.menu a{color:var(--white);font-size:11px;font-weight:600;letter-spacing:.5px;text-decoration:none}
.burger{width:24px;display:flex;flex-direction:column;gap:6px;margin-left:6px}
.burger i{height:2px;background:var(--white);display:block}
.hero-body{position:absolute;top:212px;left:0;width:1200px;text-align:center;color:var(--white)}
.hero-body .name{font-size:50px;color:var(--white);letter-spacing:-1px}
.hero-body p{font-family:"Roboto Slab",Georgia,serif;font-size:23px;line-height:40px;margin-top:18px}
.hero-body p b{color:var(--orange);font-weight:400}
.hero-body .actions{margin-top:26px;display:flex;gap:34px;justify-content:center}
.hero-body .actions .btn{width:172px;padding:0}
.dots{position:absolute;right:48px;top:290px;display:flex;flex-direction:column;gap:14px}
.dots i{width:8px;height:8px;border-radius:50%;background:rgba(255,255,255,.55);display:block}
.scroll{position:absolute;left:580px;top:574px}

/* welcome */
.welcome{top:710px}
.welcome h2{font-size:37px}
.welcome p{width:930px;margin:28px auto 0;font-size:12px;line-height:24px}
.how{top:940px}
.how h2{font-size:37px}
.how h3{font-size:21px;margin-top:14px;font-weight:400;color:var(--ink)}
.steps{position:absolute;top:150px;left:0;width:1200px;display:flex;justify-content:center;gap:60px}
.step{width:290px;text-align:center}
.step h4{font-size:16px;font-weight:400;color:var(--ink);margin-top:16px}
.step p{font-size:12px;line-height:24px;margin-top:12px}
.arrow{position:absolute;top:205px;width:40px;height:40px;border:1px solid #cfd2d5;border-radius:50%;display:flex;align-items:center;justify-content:center}

/* company */
.company{top:1388px;height:377px;background:linear-gradient(180deg,var(--city-a),var(--city-b));color:var(--white)}
.company h2{color:var(--white);font-size:36px;margin-top:88px}
.company p{font-size:16px;line-height:36px;width:760px;margin:16px auto 0}
.company .btn{margin-top:28px;width:180px;padding:0}

/* features */
.features{top:1820px}
.features h2{font-size:37px}
.features .intro{width:860px;margin:22px auto 0;font-size:12px;line-height:24px}
.grid{position:absolute;top:170px;left:100px;width:1030px;display:grid;grid-template-columns:repeat(3,350px);row-gap:44px}
.feat{display:flex;gap:18px}
.feat .ico{width:52px;height:52px;border:1.5px solid var(--blue);border-radius:50%;flex:none;display:flex;align-items:center;justify-content:center}
.feat h4{font-size:14px;font-weight:600;color:var(--ink)}
.feat p{font-size:11px;line-height:24px;margin-top:6px;width:200px}
.features .more{position:absolute;top:463px;left:510px;width:180px;padding:0;text-align:center}

/* testimonial */
.testimonial{top:2407px;height:373px;background:linear-gradient(90deg,var(--testi-a) 0%,#5d554d 45%,var(--testi-b) 100%);color:var(--white)}
.testimonial .quote{margin-top:106px}
.testimonial p{font-size:15px;line-height:32px;width:860px;margin:16px auto 0}
.testimonial .who{font-size:11px;font-weight:700;letter-spacing:1px;margin-top:20px}
.testimonial .pager{margin-top:22px;display:flex;justify-content:center;gap:5px}
.testimonial .pager i{width:5px;height:5px;border-radius:50%;background:rgba(255,255,255,.5);display:block}
.testimonial .pager i:first-child{background:var(--white)}

/* partners */
.partners{top:2780px;height:125px;display:flex;justify-content:space-around;align-items:center;padding:0 110px;border-bottom:1px solid var(--line)}
.partner{width:110px;height:34px;background:#d6d8da;border-radius:4px}
.partner.round{width:96px;border-radius:17px}
.partner.sq{width:46px;height:46px}

/* footer */
.footer{top:2940px;height:309px}
.cols{position:absolute;left:100px;top:14px;display:flex}
.col h5{font-size:14px;font-weight:600;color:var(--blue);margin-bottom:14px}
.col ul{list-style:none}
.col li{font-size:11px;line-height:24px;color:var(--text)}
.col:nth-child(1){width:173px}.col:nth-child(2){width:240px}.col:nth-child(3){width:189px}.col:nth-child(4){width:196px}
.social{display:flex;gap:7px;margin-top:12px}
.social i{width:26px;height:26px;border-radius:50%;background:#c7cacd;display:block}
.col .brand{font-size:46px;margin-top:18px;display:block}
.bottom{position:absolute;left:100px;right:100px;top:230px;border-top:1px solid var(--line);text-align:center;font-size:10px;padding-top:18px}
</style>
</head>
<body>

<header class="hero">
  <div class="hero-shade" role="img" aria-label="Photograph of hands holding a payment card over a laptop keyboard"></div>
  <nav class="nav">
    <span class="brand">fenwu</span>
    <div class="menu">
      <a>HOME</a><a>ABOUT US</a><a>SERVICES</a><a>FEATURES</a><a>TESTIMONIALS</a><a>CONTACT US</a>
      <span class="burger"><i></i><i></i><i></i></span>
    </div>
  </nav>
  <div class="hero-body">
    <div class="name">fenwu</div>
    <p>We are a new account-to-account payment product for use in<br>the Single European Payment Area <b>(SEPA)</b></p>
    <div class="actions"><span class="btn">Join with us!</span><span class="btn">Get in touch!</span></div>
  </div>
  <div class="dots"><i></i><i></i><i></i><i></i></div>
  <svg class="scroll" width="40" height="40" viewBox="0 0 40 40"><circle cx="20" cy="20" r="18.5" fill="none" stroke="#fff" stroke-width="1.5"/><path d="M13 17l7 7 7-7" fill="none" stroke="#fff" stroke-width="1.5"/></svg>
</header>

<section class="welcome center">
  <h2 class="slab">Welcome to fenwu</h2>
  <p>As a little more detail on how things work, though, our end customers will arrive at our site through redirection from our merchant partners (a number of whom are large multi-national companies) who have offered our services as an alternative to credit card payments. They will be able to set up a SEPA direct debit mandate online in just a few pages, secure that with a password and use it to pay both immediately and in future with a simple confirmation of the password… a quick, easy checkout.</p>
</section>

<section class="how center">
  <h2 class="slab">How it works</h2>
  <h3 class="slab">They will be able to set up a SEPA direct debit mandate online</h3>
  <span class="arrow" style="left:64px"><svg width="12" height="12" viewBox="0 0 12 12"><path d="M8 1L3 6l5 5" fill="none" stroke="#aaa" stroke-width="1.3"/></svg></span>
  <span class="arrow" style="left:1100px"><svg width="12" height="12" viewBox="0 0 12 12"><path d="M4 1l5 5-5 5" fill="none" stroke="#aaa" stroke-width="1.3"/></svg></span>
  <div class="steps">
    <div class="step">
      <svg width="80" height="76" viewBox="0 0 80 76" fill="none" stroke="#1b9ad6" stroke-width="2.4"><circle cx="38" cy="20" r="14"/><path d="M10 72c0-18 12-28 28-28 6 0 11 1 15 4"/><path d="M10 72h36"/><circle cx="58" cy="58" r="13"/><rect x="53" y="57" width="10" height="8"/><path d="M55 57v-3a3 3 0 016 0v3"/></svg>
      <h4>Secure Password</h4>
      <p>Lorem Ipsum is simply dummy text of the printing and typesetting industry. has been the industry's standard dummy text...</p>
    </div>
    <div class="step">
      <svg width="80" height="76" viewBox="0 0 80 76" fill="none" stroke="#1b9ad6" stroke-width="2.4"><path d="M40 4l28 10v22c0 18-12 30-28 36C24 66 12 54 12 36V14z"/><path d="M27 38l9 9 18-18"/></svg>
      <h4>Confirmation of Password</h4>
      <p>Lorem Ipsum is simply dummy text of the printing and typesetting industry. has been the industry's standard dummy text...</p>
    </div>
    <div class="step">
      <svg width="80" height="76" viewBox="0 0 80 76" fill="none" stroke="#1b9ad6" stroke-width="2.4"><path d="M14 30a27 27 0 0148-8"/><path d="M66 46a27 27 0 01-48 8"/><path d="M62 10v12H50M18 66V54h12"/><path d="M47 28c-2-3-5-4-8-4-4 0-7 2-7 5 0 7 16 4 16 12 0 3-3 5-8 5-4 0-7-1-9-4M40 20v36"/></svg>
      <h4>Quick Payment</h4>
      <p>Lorem Ipsum is simply dummy text of the printing and typesetting industry. has been the industry's standard dummy text...</p>
    </div>
  </div>
</section>

<section class="company center" role="img" aria-label="Photograph of tall office towers seen from below">
  <h2 class="slab">Our Company</h2>
  <p>has been in alternative payments for nearly 10 years and have strong products in Europe in the Pre-Paid Zelo/TrevinCard and Voucher space.</p>
  <span class="btn">Read more info</span>
</section>

<section class="features center">
  <h2 class="slab">Features</h2>
  <p class="intro">Lorem Ipsum is simply dummy text of the printing and typesetting industry. Lorem Ipsum has been the industry's standard dummy text ever since the 1500s, when an unknown printer took a galley of type and scrambled...</p>
  <div class="grid">
    <div class="feat"><span class="ico"><svg width="24" height="24" viewBox="0 0 24 24" fill="none" stroke="#1b9ad6" stroke-width="1.6"><path d="M3 21h18M6 18v-5M10 18V9M14 18v-7M18 18V5"/></svg></span><div><h4>Lorem Ipsum is simply</h4><p>Lorem Ipsum is simply dummy text of the printing and typesetting industry. has been the industry...</p></div></div>
    <div class="feat"><span class="ico"><svg width="24" height="24" viewBox="0 0 24 24" fill="none" stroke="#1b9ad6" stroke-width="1.6"><path d="M4 20l10-10M14 4l6 6-4 4-6-6z"/></svg></span><div><h4>Lorem Ipsum is simply</h4><p>Lorem Ipsum is simply dummy text of the printing and typesetting industry. has been the industry...</p></div></div>
    <div class="feat"><span class="ico"><svg width="24" height="24" viewBox="0 0 24 24" fill="none" stroke="#1b9ad6" stroke-width="1.6"><rect x="4" y="6" width="16" height="14" rx="1"/><path d="M9 6V4h6v2M12 11v4"/></svg></span><div><h4>Lorem Ipsum is simply</h4><p>Lorem Ipsum is simply dummy text of the printing and typesetting industry. has been the industry...</p></div></div>
    <div class="feat"><span class="ico"><svg width="24" height="24" viewBox="0 0 24 24" fill="none" stroke="#1b9ad6" stroke-width="1.6"><path d="M12 3l8 3v6c0 5-4 8-8 9-4-1-8-4-8-9V6z"/><path d="M9 12l2 2 4-4"/></svg></span><div><h4>Lorem Ipsum is simply</h4><p>Lorem Ipsum is simply dummy text of the printing and typesetting industry. has been the industry...</p></div></div>
    <div class="feat"><span class="ico"><svg width="24" height="24" viewBox="0 0 24 24" fill="none" stroke="#1b9ad6" stroke-width="1.6"><path d="M4 5h13v9H9l-4 3v-3H4z"/><path d="M17 9h3v8h-1v3l-3-3h-5v-3"/></svg></span><div><h4>Lorem Ipsum is simply</h4><p>Lorem Ipsum is simply dummy text of the printing and typesetting industry. has been the industry...</p></div></div>
    <div class="feat"><span class="ico"><svg width="24" height="24" viewBox="0 0 24 24" fill="none" stroke="#1b9ad6" stroke-width="1.6"><path d="M6 3h9l4 4v14H6z"/><path d="M9 10h7M9 13h7M9 16h5"/></svg></span><div><h4>Lorem Ipsum is simply</h4><p>Lorem Ipsum is simply dummy text of the printing and typesetting industry. has been the industry...</p></div></div>
  </div>
  <span class="btn more">View more features</span>
</section>

<section class="testimonial center" role="img" aria-label="Photograph of a smiling customer reading beside a window">
  <svg class="quote" width="30" height="24" viewBox="0 0 30 24" fill="#fff"><path d="M0 24V13C0 5 4 1 11 0v5c-3 1-5 3-5 7h5v12zM17 24V13c0-8 4-12 11-13v5c-3 1-5 3-5 7h5v12z"/></svg>
  <p>Lorem Ipsum is simply dummy text of the printing and typesetting industry. Lorem Ipsum has been the industry's standard dummy text ever since the 1500s, when an unknown printer took a galley of type and scrambled</p>
  <div class="who">- LORIN VASQUEL -</div>
  <div class="pager"><i></i><i></i><i></i></div>
</section>

<section class="partners">
  <span class="partner"></span>
  <span class="partner round"></span>
  <span class="partner sq"></span>
  <span class="partner round"></span>
  <span class="partner sq"></span>
  <span class="partner round"></span>
</section>

<footer class="footer">
  <div class="cols">
    <div class="col"><h5>Welcome</h5><ul><li>Home</li><li>About us</li><li>Services</li><li>Features</li><li>Testimonials</li><li>Contact us</li></ul></div>
    <div class="col"><h5>How it works</h5><ul><li>Secure Paswword</li><li>Secure pay</li><li>Confirmation of Password</li><li>Quick Payment</li><li>Easy checkout</li></ul></div>
    <div class="col"><h5>Support</h5><ul><li>Knowledge Center</li><li>Support Forums</li><li>Documentation</li><li>Support Home</li><li>Developer Center</li><li>Partner Locator</li></ul></div>
    <div class="col"><h5>Information</h5><ul><li>Privacy Statement</li><li>Website Terms</li><li>Trademarks</li><li>Sitemap</li><li>Feedback</li></ul></div>
    <div class="col"><h5>Follow us</h5><ul><li>Connect with our social network</li></ul>
      <div class="social"><i></i><i></i><i></i><i></i><i></i></div>
      <span class="brand">fenwu</span>
    </div>
  </div>
  <div class="bottom">© 2016. Fenwu. All rights reserved</div>
</footer>

</body>
</html>
```